Business Card Makeover. Recreate a sleek modern design for our business card.

DO NOT COPY OUR CURRENT DESIGN. MUST BE ONE SIDED BUSINESS CARD.
Create a new business card design, using our new logo. Attached is a sample of our current design and new logo. Please note the address and email will change. The new address is 412 Corvell Bayside Grove 30917 and our website will be www.delmarhollis.example.

We are an architectural and interior design firm. We prefer a clean modern look. Something that is refined and emulates excellence.

Industry/Entity Type

Architecture

Contact Information for Business Card

clean modern look, please do not copy our attached design.

Font styles to use
Other font styles liked:
• see attached business card font

Colors

Designer to choose colors to be used in the design.

Requirements
Must have
• Must have a modern appeal and resemble our current branding.
Nice to have
• modern font, our logo, legible name and titles progressive design
Should not have
• Do not add colors not reflected in our branding. Should not look like our current card.

```html
<!DOCTYPE html>
<html lang="en">
<head>
<meta charset="utf-8">
<title>Delmar Hollis – Business Cards</title>
<link href="https://fonts.googleapis.com/css2?family=Jost:wght@500;600&family=Montserrat:wght@400;500&family=Didact+Gothic&display=swap" rel="stylesheet">
<style>
  :root {
    --stage: #e4e6e7;
    --paper: #ffffff;
    --ink: #1d1f22;
    --brand-blue: #1a8cf0;
    --brand-grey: #7c7f82;
  }
  * { margin: 0; padding: 0; box-sizing: border-box; }
  html, body { width: 1200px; height: 848px; overflow: hidden; background: var(--stage); }
  .sheet { position: relative; width: 1200px; height: 848px; }
  .icon-set { position: absolute; width: 0; height: 0; overflow: hidden; }

  .card {
    position: absolute; left: 300px; width: 576px; height: 345px;
    background: var(--paper); color: var(--ink);
  }
  .card--front { top: 68px; }
  .card--second { top: 434px; }

  .brand { position: absolute; left: 129px; top: 46px; display: flex; align-items: center; gap: 11px; }
  .brand__dot { width: 62px; height: 62px; border-radius: 50%; background: var(--brand-blue); }
  .brand__name {
    font-family: "Jost", sans-serif; font-weight: 500; font-size: 27px;
    letter-spacing: 1px; color: var(--brand-grey); text-transform: uppercase;
  }

  .tagline {
    position: absolute; left: 0; right: 0; top: 138px; text-align: center;
    font-family: "Jost", sans-serif; font-weight: 600; font-size: 17px; letter-spacing: 0.3px;
  }

  .person { position: absolute; left: 46px; }
  .person__name { font-family: "Montserrat", sans-serif; font-weight: 500; font-size: 17px; line-height: 20px; }
  .person__role { font-family: "Montserrat", sans-serif; font-weight: 400; font-size: 15px; line-height: 20px; color: var(--brand-blue); }
  .card--front .person { top: 184px; }
  .card--second .person { top: 180px; left: 44px; }

  .rule { position: absolute; left: 47px; width: 444px; height: 2px; background: var(--ink); }
  .card--front .rule { top: 229px; }
  .card--second .rule { top: 222px; }

  .contact { position: absolute; display: flex; align-items: flex-start; gap: 7px;
    font-family: "Didact Gothic", sans-serif; font-size: 12px; line-height: 13px; white-space: nowrap; }
  .contact svg { width: 16px; height: 16px; flex: none; fill: var(--ink); margin-top: -2px; }
  .contact--wide { gap: 10px; }
</style>
</head>
<body>
<svg class="icon-set" aria-hidden="true">
  <symbol id="icon-phone" viewBox="0 0 16 16"><path d="M1 5c0-2 3-3 7-3s7 1 7 3v1h-3V5H4v1H1zM4 7h8l2 6H2z"/></symbol>
  <symbol id="icon-fax" viewBox="0 0 16 16"><path d="M4 2h8v3H4zM1 6h14v6h-3v-2H4v2H1zM5 11h6v3H5z"/></symbol>
  <symbol id="icon-mobile" viewBox="0 0 16 16"><path d="M4 0h8a1 1 0 0 1 1 1v14a1 1 0 0 1-1 1H4a1 1 0 0 1-1-1V1a1 1 0 0 1 1-1zm.5 1.5v13h7v-13z"/></symbol>
  <symbol id="icon-pin" viewBox="0 0 16 16"><path d="M8 1a5.5 5.5 0 0 0-5.5 5.5C2.5 10 8 15 8 15s5.5-5 5.5-8.5A5.5 5.5 0 0 0 8 1zm0 8a2.5 2.5 0 1 1 0-5 2.5 2.5 0 0 1 0 5z"/></symbol>
  <symbol id="icon-mail" viewBox="0 0 16 16"><circle cx="8" cy="8" r="7.8"/><g fill="none" stroke="#fff" stroke-width="1.2"><circle cx="8" cy="8" r="2"/><path d="M10 6.5v2.3a1.3 1.3 0 0 0 2.6 0V8A4.6 4.6 0 1 0 10.4 12"/></g></symbol>
  <symbol id="icon-web" viewBox="0 0 16 16"><circle cx="8" cy="8" r="7.8"/><g fill="none" stroke="#fff" stroke-width="1.1"><circle cx="8" cy="8" r="4.8"/><ellipse cx="8" cy="8" rx="2" ry="4.8"/><path d="M3.2 8h9.6"/></g></symbol>
</svg>
<main class="sheet">

  <section class="card card--front">
    <div class="brand"><span class="brand__dot"></span><span class="brand__name">Delmar Hollis</span></div>
    <p class="tagline">ARCHITECTURAL AND INTERIOR DESIGN FIRM</p>
    <div class="person">
      <p class="person__name">Marina Toller, AIA, LEED® AP</p>
      <p class="person__role">Partner / Project Architect</p>
    </div>
    <div class="rule"></div>

    <p class="contact" style="left:48px;top:241px"><svg><use href="#icon-phone"/></svg>555.210.4830</p>
    <p class="contact" style="left:48px;top:259px"><svg><use href="#icon-fax"/></svg>555.210.4831</p>
    <p class="contact" style="left:48px;top:279px"><svg><use href="#icon-pin"/></svg><span>412 Corvell Bayside Grove<br>30917</span></p>

    <p class="contact contact--wide" style="left:260px;top:244px"><svg><use href="#icon-mail"/></svg>marina@delmarhollis.example</p>
    <p class="contact contact--wide" style="left:260px;top:267px"><svg><use href="#icon-web"/></svg>www.delmarhollis.example</p>
  </section>

  <section class="card card--second">
    <div class="brand"><span class="brand__dot"></span><span class="brand__name">Delmar Hollis</span></div>
    <p class="tagline">ARCHITECTURAL AND INTERIOR DESIGN FIRM</p>
    <div class="person">
      <p class="person__name">Graham Whitby</p>
      <p class="person__role">Partner / Director of Design</p>
    </div>
    <div class="rule"></div>

    <p class="contact" style="left:48px;top:241px"><svg><use href="#icon-phone"/></svg>555.210.4830</p>
    <p class="contact" style="left:48px;top:261px"><svg><use href="#icon-fax"/></svg>555.210.4831</p>
    <p class="contact" style="left:48px;top:283px"><svg><use href="#icon-mobile"/></svg>555.318.7742</p>

    <p class="contact" style="left:260px;top:235px"><svg><use href="#icon-pin"/></svg><span>412 Corvell Bayside Grove<br>30917</span></p>
    <p class="contact" style="left:260px;top:263px"><svg><use href="#icon-mail"/></svg>graham@delmarhollis.example</p>
    <p class="contact" style="left:260px;top:286px"><svg><use href="#icon-web"/></svg>www.delmarhollis.example</p>
  </section>

</main>
</body>
</html>
```